Picket Sign Advertising For Alaska Tour Company

I would like a relator style picket sign made that I can place by the water near hotels to generate phone calls and website visits. I want to Advertise Our Daily Jet Boat Tours & Jet Ski Tours. This will be a one sided sign. You may be able to see our past brochure and flyer designs and logo. Our FB page is Halvorsen Summit Excursions and our website is halvorsensummitexcursions.com or contact number is 907-418-5963

```html
<!DOCTYPE html>
<html lang="en">
<head>
<meta charset="utf-8">
<title>Halvorsen Summit Excursions – Jet Boat &amp; Jet Ski Alaska Tours Sign</title>
<link rel="stylesheet" href="https://fonts.googleapis.com/css2?family=Oswald:wght@600;700&display=swap">
<style>
  :root {
    --page: #ffffff;
    --sign-black: #000000;
    --brush-green: #39b54a;
    --band-magenta: #cc1d7d;
    --headline-white: #ffffff;
    --web-yellow: #d6e021;
    --brand-gold: #c7a25a;
    --sky: #7fb6e6;
    --tree: #3f6b2a;
    --water: #4a86b8;
    --sun: #f4d98a;
    --gravel: #9b8a78;
  }
  html, body {
    margin: 0;
    padding: 0;
    width: 1200px;
    height: 875px;
    overflow: hidden;
    background: var(--page);
  }
  .canvas {
    position: relative;
    width: 1200px;
    height: 875px;
  }
  .sign {
    position: absolute;
    left: 310px;
    top: 27px;
    width: 580px;
    height: 820px;
    display: block;
  }
  .sign-text {
    font-family: "Oswald", "Arial Narrow", sans-serif;
    font-weight: 700;
  }
  .headline { fill: var(--headline-white); }
  .phone { fill: var(--headline-white); font-weight: 600; }
  .website { fill: var(--web-yellow); font-weight: 600; }
  .brand-name { fill: var(--brand-gold); font-weight: 600; letter-spacing: 1px; }
</style>
</head>
<body>
<main class="canvas">
  <svg class="sign" viewBox="0 0 641 906" xmlns="http://www.w3.org/2000/svg" aria-labelledby="sign-title">
    <title id="sign-title">Jet Boat &amp; Jet Ski Alaska Tours – Halvorsen Summit Excursions</title>
    <defs>
      <linearGradient id="scene-tones" x1="0" y1="0" x2="0" y2="1">
        <stop offset="0" stop-color="var(--sky)"/>
        <stop offset="0.3" stop-color="#bcd7ee"/>
        <stop offset="0.42" stop-color="var(--sun)"/>
        <stop offset="0.5" stop-color="var(--tree)"/>
        <stop offset="0.66" stop-color="var(--water)"/>
        <stop offset="0.85" stop-color="var(--gravel)"/>
        <stop offset="1" stop-color="#7d6f60"/>
      </linearGradient>
      <clipPath id="photo-strips">
        <polygon points="138,62 641,218 641,298 138,142"/>
        <polygon points="0,118 641,317 641,405 0,206"/>
        <polygon points="68,248 590,410 590,495 68,333"/>
        <polygon points="0,345 641,544 641,630 500,586 500,604 0,604"/>
      </clipPath>
    </defs>

    <rect class="sign-base" width="641" height="906" fill="var(--sign-black)"/>

    <path class="brush-stroke" fill="var(--brush-green)"
      d="M0,0 H362 L350,8 L356,14 L330,22 L338,28 L300,40 L306,46 L250,60 L258,66 L190,80 L196,86 L120,100 L126,106 L40,118 L0,124 Z"/>

    <g class="lake-photo" role="img" aria-label="Sunlit Alaskan lake with a jet ski beached on a gravel shore, shown in diagonal strips">
      <rect x="0" y="60" width="641" height="560" fill="url(#scene-tones)" clip-path="url(#photo-strips)"/>
    </g>

    <path class="headline-band" fill="var(--band-magenta)"
      d="M0,453 L641,652 L641,880 L620,872 L628,866 L560,846 L566,840 L480,814 L486,808 L380,776 L386,770 L280,738 L286,732 L180,700 L186,694 L90,664 L96,658 L20,634 L0,628 Z"/>

    <g class="brand-mark">
      <circle cx="518" cy="52" r="14" fill="var(--brand-gold)"/>
      <text class="sign-text brand-name" x="518" y="94" font-size="22" text-anchor="middle">HALVORSEN</text>
      <text class="sign-text brand-name" x="518" y="120" font-size="22" text-anchor="middle">SUMMIT</text>
      <text class="sign-text brand-name" x="518" y="146" font-size="22" text-anchor="middle">EXCURSIONS</text>
    </g>

    <text class="sign-text headline" x="48" y="535" font-size="74"
      transform="rotate(17.2 48 535)" textLength="572" lengthAdjust="spacingAndGlyphs">Jet Boat &amp; Jet Ski</text>
    <text class="sign-text headline" x="44" y="650" font-size="118"
      transform="rotate(17.2 44 650)" textLength="575" lengthAdjust="spacingAndGlyphs">Alaska Tours</text>

    <text class="sign-text phone" x="40" y="835" font-size="54" font-style="italic"
      textLength="322" lengthAdjust="spacingAndGlyphs">907-418-5963</text>
    <text class="sign-text website" x="40" y="877" font-size="32"
      textLength="405" lengthAdjust="spacingAndGlyphs">HALVORSENSUMMITEXCURSIONS.COM</text>
  </svg>
</main>
</body>
</html>
```